A new updated business card. A good first impression for new customers to our business.

I need something unique. I will attached a picture of our old rubbish cards, and also our current Logo ( I think this needs an update if you have any ideas, its very basic and budget)The best way you will get to see my business is checking our Facebook page, I don't really know what else to say, but anything you want to know, ask away.www.facebook.com/tkwashandseal/

Target Market(s)

Home owners

Industry/Entity Type

Business

Contact Information for Business Card

T&K's Pressure Cleaning & Concrete Sealing
Maya 0492 615 370 maya@tkwashandseal.com
Dylan 0431 528 906 dylan@tkwashandseal.com

FB: www.facebook.com/tkwashandseal/
Website: www.tkwashandseal.net (This is pretty rubbish- we don't really use it)

100% customer satisfaction guaranteed

All aspects of Hi-Pressure Cleaning
Sealing & Re-Sealing
Roof Cleaning
Colour sealing
Decorative coatings

Free no obligation quotes

Requirements
Must have
• NO OBLIGATION FREE quotes
• 100% Customer satisfaction guaranteed
• Can you please add both names, contact details and email address on one card.
• Dylan 0431 528 906
• dylan@tkwashandseal.com
• Maya 0492 615 370
• maya@tkwashandseal.com
• Please change the services:
• Hot/Cold Hi-Pressure Cleaning
• Sealing & Re-Sealing
• Roof Cleaning
• Colour Sealing
• Decorative Coatings
• Concrete Honing
• Thanks
Nice to have
• Something a bit different, something eye catching.l

```html
<!DOCTYPE html>
<html lang="en">
<head>
<meta charset="utf-8">
<title>T&amp;K's Pressure Cleaning – Business Card</title>
<link rel="stylesheet" href="https://fonts.googleapis.com/css2?family=Source+Sans+3:ital,wght@0,400;0,600;0,700;1,700&display=swap">
<style>
  :root {
    --backdrop: #8e8e8e;
    --card: #f1f1f1;
    --brand-red: #cf1520;
    --ink: #545454;
    --ink-dark: #3a3a3a;
  }
  * { margin: 0; padding: 0; box-sizing: border-box; }
  html, body {
    width: 1105px;
    height: 1200px;
    overflow: hidden;
    background: var(--backdrop);
    font-family: "Source Sans 3", "Myriad Pro", Arial, sans-serif;
  }
  .card {
    position: absolute;
    left: 180px;
    width: 746px;
    height: 425px;
    background: var(--card);
  }
  .card--front { top: 130px; }
  .card--back  { top: 645px; }

  .brand {
    position: absolute;
    left: 372px;
    top: 52px;
    width: 330px;
    display: flex;
    align-items: center;
    gap: 14px;
  }
  .brand__dot {
    flex: none;
    width: 22px;
    height: 22px;
    border-radius: 50%;
    background: var(--brand-red);
  }
  .brand__name {
    color: var(--brand-red);
    font-weight: 700;
    font-size: 25px;
    line-height: 1.15;
  }

  .contact-name {
    position: absolute;
    left: 39px;
    color: var(--brand-red);
    font-weight: 700;
    font-size: 27px;
    line-height: 1;
  }
  .contact-line {
    position: absolute;
    display: flex;
    align-items: center;
    gap: 10px;
    color: var(--ink);
    font-size: 19px;
    line-height: 1;
  }
  .contact-line svg { flex: none; width: 16px; height: 16px; fill: var(--brand-red); }
  .contact-line .marker-square { width: 15px; height: 15px; background: var(--brand-red); flex: none; }
  .contact-line .marker-circle { width: 15px; height: 15px; background: var(--brand-red); border-radius: 50%; flex: none; }

  .tagline {
    position: absolute;
    left: 36px;
    top: 376px;
    color: var(--brand-red);
    font-style: italic;
    font-weight: 700;
    font-size: 21px;
    letter-spacing: 1.3px;
  }

  .services {
    position: absolute;
    left: 39px;
    top: 170px;
    list-style: none;
  }
  .services li {
    position: relative;
    padding-left: 16px;
    height: 31px;
    color: var(--ink);
    font-size: 20px;
    line-height: 22px;
  }
  .services li::before {
    content: "";
    position: absolute;
    left: 0;
    top: 8px;
    width: 6px;
    height: 6px;
    border-radius: 50%;
    background: var(--brand-red);
  }
</style>
</head>
<body>

<section class="card card--front">
  <div class="brand">
    <span class="brand__dot"></span>
    <span class="brand__name">T&amp;K's Pressure Cleaning &amp; Concrete Sealing</span>
  </div>

  <h2 class="contact-name" style="top:186px">Dylan</h2>
  <div class="contact-line" style="left:39px;top:220px">
    <svg viewBox="0 0 16 16"><path d="M3.2 1.2l2.6 2.9-1.5 1.9c.9 2 2.5 3.6 4.5 4.6l1.9-1.5 2.9 2.5-1.5 2.4C7.2 13.7 2.3 8.8 1 3z"/></svg>
    <span>0431 528 906</span>
  </div>
  <div class="contact-line" style="left:39px;top:248px">
    <svg viewBox="0 0 16 16"><path d="M1 3h14v10H1z M1.8 3.6L8 8.6l6.2-5" fill="var(--brand-red)" stroke="var(--card)" stroke-width="1.2"/></svg>
    <span>dylan@tkwashandseal.com</span>
  </div>

  <h2 class="contact-name" style="top:287px">Maya</h2>
  <div class="contact-line" style="left:39px;top:320px">
    <svg viewBox="0 0 16 16"><path d="M3.2 1.2l2.6 2.9-1.5 1.9c.9 2 2.5 3.6 4.5 4.6l1.9-1.5 2.9 2.5-1.5 2.4C7.2 13.7 2.3 8.8 1 3z"/></svg>
    <span>0492 615 370</span>
  </div>
  <div class="contact-line" style="left:39px;top:349px">
    <svg viewBox="0 0 16 16"><path d="M1 3h14v10H1z M1.8 3.6L8 8.6l6.2-5" fill="var(--brand-red)" stroke="var(--card)" stroke-width="1.2"/></svg>
    <span>maya@tkwashandseal.com</span>
  </div>

  <div class="contact-line" style="left:404px;top:320px">
    <span class="marker-square"></span>
    <span>tkwashandseal</span>
  </div>
  <div class="contact-line" style="left:404px;top:349px">
    <span class="marker-circle"></span>
    <span>www.tkwashandseal.net</span>
  </div>

  <p class="tagline">100% customer satisfaction guaranteed</p>
</section>

<section class="card card--back">
  <div class="brand">
    <span class="brand__dot"></span>
    <span class="brand__name">T&amp;K's Pressure Cleaning &amp; Concrete Sealing</span>
  </div>

  <ul class="services">
    <li>Hot/Cold Hi-Pressure Cleaning</li>
    <li>Sealing &amp; Re-Sealing</li>
    <li>Roof Cleaning</li>
    <li>Colour Sealing</li>
    <li>Decorative Coatings</li>
    <li>Concrete Honing</li>
  </ul>

  <p class="tagline" style="top:372px">Free no obligation quotes</p>
</section>

</body>
</html>
```